National online rug retailer needs a home page design

See the FloorNest logo and create a home page design around that color theme. Details are spelled out in word document uploaded below.

Apparently this website did not take my attachement showing the logo and basic requirements.  If you would send me your email address, I will send you the attachment directly.
Best regards,
Tom Vance
tvance@mrdcorp.example

Target Market(s)

The target market is home owners 25 to 75 years old with combined incomes over $100,000 per year.

Industry/Entity Type

Online

Requirements
Must have
• Lots of white space with black letters and creative use of red and possibly one other color. Would like a compelling call to action button.

```html
<!DOCTYPE html>
<html lang="en">
<head>
<meta charset="utf-8">
<title>FloorNest.com – Home</title>
<link href="https://fonts.googleapis.com/css2?family=Mulish:wght@400;600;700;800&display=swap" rel="stylesheet">
<style>
:root{
  --red:#e3000f;
  --red-dark:#b5000b;
  --ink:#222;
  --text:#444;
  --muted:#777;
  --line:#ddd;
  --panel:#f4f4f4;
  --footer-bar:#555;
}
*{box-sizing:border-box;margin:0;padding:0}
html,body{width:961px;height:1200px;overflow:hidden;background:#fff}
body{position:relative;font-family:"Mulish",sans-serif;color:var(--text);font-size:10px}
.abs{position:absolute}
a{color:inherit;text-decoration:none}

/* header */
.brand{left:102px;top:20px;display:flex;align-items:center;gap:6px}
.brand-mark{width:30px;height:30px;background:var(--red)}
.brand-name{font-size:30px;font-weight:600;color:var(--ink);letter-spacing:-.5px}
.tagline{left:173px;top:67px;font-size:9px;color:var(--muted)}
.search{left:390px;top:38px;width:178px;height:28px;border:1px solid #ccc;font-size:8.5px;color:#999;padding:9px 8px;letter-spacing:.3px}
.search-btn{left:571px;top:38px;width:28px;height:28px;background:#777;display:flex;align-items:center;justify-content:center}
.cart-line{left:652px;top:23px;font-size:9.5px;color:var(--muted)}
.cart-line b{color:var(--ink);font-weight:600}
.order{left:651px;top:41px;font-size:13px;color:var(--muted)}
.order .phone{color:var(--red)}
.account{left:652px;top:63px;font-size:9.5px;color:var(--muted);display:flex;gap:8px;align-items:center}

/* nav */
.nav{left:102px;top:105px;width:757px;height:38px;background:var(--red);border:2px solid var(--red-dark);display:flex;align-items:center;justify-content:space-between;padding:0 14px;color:#fff;font-weight:700;font-size:10.5px;letter-spacing:.3px}
.nav .sep{font-weight:400;opacity:.9}

/* hero */
.hero{left:102px;top:156px;width:757px;height:234px;border:1px solid #ccc}
.hero-photo{left:109px;top:161px;width:743px;height:224px;background:linear-gradient(90deg,#d8d8d8 0%,#cfcfcf 35%,#8e9aa6 55%,#6f7c8a 75%,#9aa2ab 100%)}
.hero-copy{left:139px;top:198px;color:var(--red)}
.hero-copy .save{font-size:24px;font-weight:400}
.hero-copy .pct{font-size:56px;font-weight:400;line-height:1}
.hero-copy .ship{font-size:21px;margin-top:-2px}
.hero-copy .sub{font-size:18px;color:#555;margin-top:6px;line-height:1.2;letter-spacing:.5px}

/* sidebar */
.browse{left:102px;top:414px;width:180px}
.browse-head{height:34px;background:var(--red);border:2px solid var(--red-dark);border-radius:4px 4px 0 0;color:#fff;font-size:14px;font-weight:600;padding:6px 14px}
.browse-item{height:33px;border:1px solid var(--line);border-top:none;background:linear-gradient(#fff,#f3f3f3);display:flex;justify-content:space-between;align-items:center;padding:0 12px 0 14px;font-size:9.5px;font-weight:800;color:#333}
.browse-item:last-child{border-radius:0 0 4px 4px}
.browse-item .plus{font-weight:400;font-size:12px;color:#555}
.also{left:102px;top:732px;width:180px;height:155px;border:1px solid #ccc}
.also-photo{left:106px;top:737px;width:172px;height:143px;background:radial-gradient(circle at 50% 40%,#f2f2f2,#d6d6d6)}
.also-cap{left:106px;top:850px;width:172px;height:30px;background:#444;color:#fff;font-size:14px;font-weight:600;letter-spacing:.8px;display:flex;align-items:center;justify-content:center}

/* featured */
.feat-title{left:305px;top:415px;font-size:11.5px;font-weight:700;color:#444}
.feat-rule{left:447px;top:416px;width:369px;height:12px;background:repeating-linear-gradient(135deg,#ccc 0 1px,#fff 1px 4px)}
.feat-arrows{left:838px;top:414px}
.card{width:176px;height:207px;border:1px solid var(--line);background:#fff;box-shadow:0 6px 6px -5px rgba(0,0,0,.35)}
.card-photo{position:absolute;left:9px;top:7px;width:161px;height:120px}
.card-name{position:absolute;left:18px;top:144px;font-size:11px;color:#555}
.card-btn{position:absolute;left:18px;top:165px;width:68px;height:21px;background:var(--red);border:1px solid var(--red-dark);box-shadow:0 0 0 1px #f2a0a5;color:#fff;font-size:8px;font-weight:800;display:flex;align-items:center;justify-content:center}
.card-old{position:absolute;left:101px;top:164px;font-size:10.5px;color:#555;text-decoration:line-through}
.card-new{position:absolute;left:101px;top:176px;font-size:11px;color:var(--red)}
.ribbon{position:absolute;left:-2px;top:-2px}

/* footer */
.footer{left:102px;top:918px;width:757px;height:240px;background:var(--panel);border:1px solid #e4e4e4}
.fcol{top:933px}
.fcol h4{font-size:11.5px;font-weight:700;color:#444;margin-bottom:26px}
.fcol li{list-style:none;font-size:9.8px;line-height:15.2px;color:#555}
.frule{left:123px;top:958px;width:709px;height:1px;background:#ddd}
.pay{left:582px;top:983px;display:flex;gap:4px}
.pay span{width:23px;height:16px;border-radius:2px;border:1px solid #ccc}
.badges{left:578px;top:1022px;display:flex;gap:6px;align-items:center}
.copy{left:102px;top:1158px;width:757px;height:42px;background:var(--footer-bar);color:#ccc;font-size:10px;display:flex;align-items:center;justify-content:center}
</style>
</head>
<body>

<!-- header -->
<div class="abs brand"><span class="brand-mark"></span><span class="brand-name">FloorNest.com</span></div>
<div class="abs tagline">for domestic and heirloom values</div>
<div class="abs search">Enter a keyword or item</div>
<div class="abs search-btn">
  <svg width="14" height="14" viewBox="0 0 14 14"><circle cx="6" cy="6" r="4.3" fill="none" stroke="#fff" stroke-width="1.6"/><line x1="9.2" y1="9.2" x2="12.5" y2="12.5" stroke="#fff" stroke-width="1.8"/></svg>
</div>
<div class="abs cart-line">Items (0) &nbsp;<b>Total $0.00</b> &nbsp;View Cart &nbsp;| &nbsp;Checkout</div>
<div class="abs order">Order Toll-Free &nbsp;: &nbsp;<span class="phone">1-800-555-0142</span></div>
<div class="abs account">
  <span>My Account &nbsp;|&nbsp; Sign</span>
  <span><svg width="9" height="9" viewBox="0 0 10 10"><path d="M1 1h6v4H4L2 7V5H1z" fill="#333"/><path d="M8 3h1v4H8v2L6 7H4V6h4z" fill="#333"/></svg> Live Chat</span>
  <span><svg width="9" height="9" viewBox="0 0 10 10"><circle cx="5" cy="3" r="2.3" fill="#333"/><path d="M0.5 10c0-3 2-4.5 4.5-4.5S9.5 7 9.5 10z" fill="#333"/></svg> Online</span>
</div>

<!-- navigation -->
<nav class="abs nav">
  <a>HOME</a><span class="sep">I</span><a>SELECTION GUIDES</a><span class="sep">I</span><a>RUG CARE</a><span class="sep">I</span><a>FAQ</a><span class="sep">I</span><a>RETURN POLICY</a><span class="sep">I</span><a>FREE SHIPPING</a><span class="sep">I</span><a>CLEARANCE RUGS</a>
</nav>

<!-- hero -->
<div class="abs hero"></div>
<div class="abs hero-photo" role="img" aria-label="Close-up of a woven rag rug with fringed edge on a pale grey background"></div>
<div class="abs hero-copy">
  <div><span class="save">SAVE</span> <span class="pct">75%</span></div>
  <div class="ship">+ FREE SHIPPING</div>
  <div class="sub">FOR DOMESTIC AND<br>HERILOOM VALUES</div>
</div>

<!-- browse -->
<div class="abs browse">
  <div class="browse-head">Browse</div>
  <div class="browse-item">RUG THEME<span class="plus">+</span></div>
  <div class="browse-item">COLOR WAY<span class="plus">+</span></div>
  <div class="browse-item">SIZE<span class="plus">+</span></div>
  <div class="browse-item">SHAPE<span class="plus">+</span></div>
  <div class="browse-item">FIBER CONTENT<span class="plus">+</span></div>
  <div class="browse-item">MFGR. BRAND<span class="plus">+</span></div>
  <div class="browse-item">MFGR.COLLECTION<span class="plus">+</span></div>
  <div class="browse-item">PRICE<span class="plus">+</span></div>
</div>
<div class="abs also"></div>
<div class="abs also-photo" role="img" aria-label="White shag rug texture"></div>
<div class="abs also-cap">YOU MAY ALSO LIKE</div>

<!-- featured -->
<div class="abs feat-title">FEATURED PRODUCTS</div>
<div class="abs feat-rule"></div>
<div class="abs feat-arrows">
  <svg width="22" height="12" viewBox="0 0 22 12"><path d="M6 2L2 6l4 4" fill="none" stroke="#333" stroke-width="2"/><path d="M16 2l4 4-4 4" fill="none" stroke="#333" stroke-width="2"/></svg>
</div>

<!-- row 1 -->
<div class="abs card" style="left:303px;top:449px">
  <div class="card-photo" role="img" aria-label="Black rug with colourful overlapping circles" style="background:linear-gradient(135deg,#2a2420,#4a3a2e)"></div>
  <svg class="ribbon" width="60" height="60" viewBox="0 0 60 60"><path d="M0 30L30 0h26L0 56z" fill="#777"/><text x="16" y="30" transform="rotate(-45 16 30)" fill="#fff" font-size="10" font-weight="800" font-family="Mulish,sans-serif">NEW</text></svg>
  <div class="card-name">Lorem Ipsum Dolor</div>
  <div class="card-btn">ADD TO CART</div>
  <div class="card-old">$55.67</div><div class="card-new">$48.67</div>
</div>
<div class="abs card" style="left:491px;top:449px">
  <div class="card-photo" role="img" aria-label="Grey geometric rug in a bright modern living room" style="background:linear-gradient(180deg,#d8d8d8,#a9a9a9)"></div>
  <div class="card-name">Lorem Ipsum Dolor</div>
  <div class="card-btn">ADD TO CART</div>
  <div class="card-old">$55.67</div><div class="card-new">$48.67</div>
</div>
<div class="abs card" style="left:682px;top:449px">
  <div class="card-photo" role="img" aria-label="Cream rug with red and black card-suit border on wood floor" style="background:radial-gradient(circle,#e9e2cc 45%,#7a2a20 80%)"></div>
  <svg class="ribbon" width="60" height="60" viewBox="0 0 60 60"><path d="M0 30L30 0h26L0 56z" fill="#777"/><text x="16" y="30" transform="rotate(-45 16 30)" fill="#fff" font-size="10" font-weight="800" font-family="Mulish,sans-serif">NEW</text></svg>
  <div class="card-name">Lorem Ipsum Dolor</div>
  <div class="card-btn">ADD TO CART</div>
  <div class="card-old">$55.67</div><div class="card-new">$48.67</div>
</div>

<!-- row 2 -->
<div class="abs card" style="left:303px;top:679px">
  <div class="card-photo" role="img" aria-label="Red, grey and white swirl shag rug before a sofa" style="background:linear-gradient(180deg,#b8463f 0%,#ddd 40%,#9a8d88 100%)"></div>
  <svg class="ribbon" width="60" height="60" viewBox="0 0 60 60"><path d="M0 30L30 0h26L0 56z" fill="#777"/><text x="16" y="30" transform="rotate(-45 16 30)" fill="#fff" font-size="10" font-weight="800" font-family="Mulish,sans-serif">NEW</text></svg>
  <div class="card-name">Lorem Ipsum Dolor</div>
  <div class="card-btn">ADD TO CART</div>
  <div class="card-old">$55.67</div><div class="card-new">$48.67</div>
</div>
<div class="abs card" style="left:491px;top:679px">
  <div class="card-photo" role="img" aria-label="Red rug with curved lines in a bedroom" style="background:linear-gradient(180deg,#efe8dc 0%,#d8c7a8 45%,#a8241c 70%,#8a1a14 100%)"></div>
  <div class="card-name">Lorem Ipsum Dolor</div>
  <div class="card-btn">ADD TO CART</div>
  <div class="card-old">$55.67</div><div class="card-new">$48.67</div>
</div>
<div class="abs card" style="left:682px;top:679px">
  <div class="card-photo" role="img" aria-label="Navy patterned traditional rug with ornate border" style="background:radial-gradient(circle,#1e2a4a 40%,#7a4a30 85%)"></div>
  <svg class="ribbon" width="60" height="60" viewBox="0 0 60 60"><path d="M0 30L30 0h26L0 56z" fill="#777"/><text x="16" y="30" transform="rotate(-45 16 30)" fill="#fff" font-size="10" font-weight="800" font-family="Mulish,sans-serif">NEW</text></svg>
  <div class="card-name">Lorem Ipsum Dolor</div>
  <div class="card-btn">ADD TO CART</div>
  <div class="card-old">$55.67</div><div class="card-new">$48.67</div>
</div>

<!-- footer -->
<div class="abs footer"></div>
<div class="abs fcol" style="left:123px"><h4>Customer Services</h4><ul>
  <li>Shipping</li><li>Return Policy</li><li>Privacy Policy</li><li>Ordering &amp; Delivery</li><li>Checklist</li><li>Terms of Use</li><li>Terms of Sale</li><li>Contact Us</li><li>Environmental Policy</li></ul></div>
<div class="abs fcol" style="left:278px"><h4>Resources</h4><ul>
  <li>Product Articles</li><li>Learning Center</li><li>Help</li><li>Refer A Friend</li><li>FloorNest Blog</li><li>Room Scene Viewer</li><li>Site Map</li><li>FAQ</li><li>Customer Testimonials</li><li>Photo Gallery</li></ul></div>
<div class="abs fcol" style="left:423px"><h4>Corporate Info</h4><ul>
  <li>About FloorNest.com</li><li>Careers</li><li>Affiliates</li></ul></div>
<div class="abs fcol" style="left:581px"><h4>Payments &amp; Security</h4></div>
<div class="abs frule"></div>
<div class="abs pay">
  <span style="background:#2a4c9a"></span><span style="background:#f3f3f3"></span><span style="background:#1a3f8f"></span><span style="background:#3a8fc9"></span><span style="background:#f2c230"></span>
  <span style="width:86px;border:none;background:#dde4ee"></span>
</div>
<div class="abs badges">
  <svg width="40" height="40"><circle cx="20" cy="20" r="19" fill="#e2c25a"/></svg>
  <svg width="38" height="38"><circle cx="19" cy="19" r="18" fill="#f0d24a"/></svg>
  <svg width="54" height="24"><rect width="54" height="24" rx="3" fill="#ddd" stroke="#aaa"/></svg>
  <svg width="52" height="30"><rect width="52" height="24" fill="#2b5aa6"/></svg>
  <svg width="62" height="34"><rect y="8" width="62" height="22" fill="#e4e4e4" stroke="#999"/></svg>
</div>
<div class="abs copy">© Copyrights 2013 &nbsp;FloorNest. All rights Reserved</div>

</body>
</html>
```